Personal Chef Business Card Design

My company, Simmered, is a personal in-home chef service that caters to clients' needs, but I am not a caterer. The types of services that I provide range from : weekly menus for busy families, special menus for specific diets, custom menus, private parties, intimate dinners, and brunch parties. My cooking style is seasonal and simple with the option of a variety of cuisines. I like colorful and simple business cards. My business is just getting started as I will be the only employee for now. I would like to be able to use the design on the card for my logo also. I don't know if logo design is a different service altogether.

If you can convince me to go with double-sided, then so be it, but until then, I'll stick with singe-sided.

Target Market(s)

busy families, health conscious, private parties, brunch parties, dinner parties

Industry/Entity Type

Chef

Contact Information for Business Card

Owen Talbot
owentalbot@kestrelmail.com
555-418-2937
Simmered Personal Chef Service
Serving the Riverton/Ashford area

Font styles to use
Serif
Sans Serif
Decorative
Script
Other font styles liked:
• Anything

Requirements
Must have
• I will be using the illustration as my logo so that I can use it for promotional merchandise.

```html
<!DOCTYPE html>
<html lang="en">
<head>
<meta charset="utf-8">
<title>Simmered Personal Chef Service – Business Card</title>
<link href="https://fonts.googleapis.com/css2?family=Lato:wght@300;400;700&display=swap" rel="stylesheet">
<style>
  :root {
    --page: #ebe7e1;
    --orange: #e0751c;
    --orange-deep: #c9621a;
    --orange-light: #f0a052;
    --charcoal: #2b2b2b;
    --paper: #ffffff;
    --ink-light: #f3f3f3;
  }
  * { box-sizing: border-box; margin: 0; padding: 0; }
  html, body {
    width: 1200px; height: 823px; overflow: hidden;
    background: var(--page);
    font-family: "Lato", Arial, sans-serif;
  }
  .canvas { position: relative; width: 1200px; height: 823px; }
  .card {
    position: absolute; left: 390px; top: 44px;
    width: 420px; height: 735px;
    background: var(--orange);
    overflow: hidden;
    box-shadow: 0 6px 18px rgba(0,0,0,0.18);
  }
  .card-shapes { position: absolute; inset: 0; }
  .brand {
    position: absolute; left: 28px; right: 0; top: 100px;
    display: flex; flex-direction: column; align-items: center; gap: 10px;
  }
  .brand-row { display: flex; align-items: center; gap: 14px; }
  .brand-dot {
    width: 34px; height: 34px; border-radius: 50%;
    background: var(--orange);
  }
  .brand-name {
    font-size: 40px; font-weight: 700; letter-spacing: 2px;
    color: var(--orange); text-transform: uppercase;
  }
  .brand-tagline {
    font-size: 16px; font-weight: 400; letter-spacing: 1px;
    color: var(--orange);
  }
  .holder {
    position: absolute; left: 0; right: 0; top: 392px;
    display: flex; align-items: center; justify-content: center; gap: 12px;
    color: var(--paper); font-size: 24px; letter-spacing: 1px;
    text-transform: uppercase;
  }
  .holder-first { font-weight: 300; }
  .holder-last { font-weight: 700; }
  .holder-icon { width: 22px; height: 22px; }
  .contacts {
    position: absolute; left: 60px; top: 560px;
    list-style: none; display: flex; flex-direction: column; gap: 30px;
  }
  .contact {
    display: flex; align-items: center; gap: 18px;
    color: var(--ink-light); font-size: 17px; font-weight: 300; letter-spacing: 0.4px;
    white-space: nowrap;
  }
  .contact-icon { width: 20px; height: 20px; flex: none; }
</style>
</head>
<body>
<main class="canvas">
  <article class="card">
    <svg class="card-shapes" viewBox="0 0 420 735" width="420" height="735" aria-hidden="true">
      <polygon points="28,0 420,0 420,230 210,320 28,262" fill="var(--paper)"/>
      <polygon points="0,370 420,300 420,420 210,480 0,440" fill="var(--orange-light)"/>
      <polygon points="0,440 210,480 0,520" fill="var(--orange-deep)"/>
      <polygon points="0,520 210,480 420,420 420,735 0,735" fill="var(--charcoal)"/>
    </svg>

    <div class="brand">
      <div class="brand-row">
        <span class="brand-dot"></span>
        <span class="brand-name">Simmered</span>
      </div>
      <span class="brand-tagline">Personal Chef Service</span>
    </div>

    <div class="holder">
      <svg class="holder-icon" viewBox="0 0 24 24" aria-hidden="true">
        <circle cx="12" cy="8" r="5" fill="var(--paper)"/>
        <path d="M3 22c0-5 4-8 9-8s9 3 9 8z" fill="var(--paper)"/>
      </svg>
      <span><span class="holder-first">Owen</span> <span class="holder-last">Talbot</span></span>
    </div>

    <ul class="contacts">
      <li class="contact">
        <svg class="contact-icon" viewBox="0 0 24 24" aria-hidden="true">
          <path d="M6.6 10.8a15 15 0 0 0 6.6 6.6l2.2-2.2a1 1 0 0 1 1-.25 11.4 11.4 0 0 0 3.6.57 1 1 0 0 1 1 1V20a1 1 0 0 1-1 1A17 17 0 0 1 3 4a1 1 0 0 1 1-1h3.5a1 1 0 0 1 1 1c0 1.25.2 2.45.57 3.6a1 1 0 0 1-.25 1z" fill="var(--ink-light)"/>
        </svg>
        <span>555-418-2937</span>
      </li>
      <li class="contact">
        <svg class="contact-icon" viewBox="0 0 24 24" aria-hidden="true">
          <circle cx="12" cy="12" r="10" fill="none" stroke="var(--ink-light)" stroke-width="2"/>
          <ellipse cx="12" cy="12" rx="4.5" ry="10" fill="none" stroke="var(--ink-light)" stroke-width="1.6"/>
          <line x1="2" y1="12" x2="22" y2="12" stroke="var(--ink-light)" stroke-width="1.6"/>
          <line x1="4" y1="7" x2="20" y2="7" stroke="var(--ink-light)" stroke-width="1.4"/>
          <line x1="4" y1="17" x2="20" y2="17" stroke="var(--ink-light)" stroke-width="1.4"/>
        </svg>
        <span>owentalbot@kestrelmail.com</span>
      </li>
      <li class="contact">
        <svg class="contact-icon" viewBox="0 0 24 24" aria-hidden="true">
          <path d="M12 2a7 7 0 0 0-7 7c0 5 7 13 7 13s7-8 7-13a7 7 0 0 0-7-7zm0 9.5A2.5 2.5 0 1 1 12 6.5a2.5 2.5 0 0 1 0 5z" fill="var(--ink-light)"/>
        </svg>
        <span>Serving the Riverton/Ashford area</span>
      </li>
    </ul>
  </article>
</main>
</body>
</html>
```